Bold, Modern, Clean "Kestrelwaymassage.com" website

Why we stand out?
We are a male and female mobile massage team. Our names are Paul and Lina. 
Kestrel Way is a Seattle based mobile massage service. Our massage is offered to the community with a goal of facilitating balance within each individual. We specialize in integrated Pain management, and sports/medical massage therapy. Every client's first assessment is attended by our male and female massage therapist team. Depending on the goals identified for an individual determines which therapist will be assigned to provide treatment, if not both.

Our passion...
Here at Kestrel Way, we have a great passion for Postural Resoration and how it is integrated into an individual's Massage treatment. We pride ourselves in being natural facilitators of healing, which takes the ego of the therapist out of the client's healing process. We strive to deliver the best massage possible by including modalities such as Neuromuscular, Myofascial release, spontaneous muscle release, postural restoration, orthopedic, and medical massage.

Our education...

We are both Graduates of Venmora, school of massage therapy. We have continuing education in medical massage, myofacial release, trigger point therapy, postural restoration, anatomy, and spontaneous muscle release. Lina is also a Certified Yoga Instructor, which amplifies her experience with flexibility and strength as it pertains to each individual. Paul's passion is Massage, stretching, and strength training to encourage postural restoration and realignment.

Our rates-

Our rates are $75/ 60 minutes, $95/ 90 minutes, and $120/ 120 minutes.

Education-
Both Lina and I worked as behavioral health professionals that specialized in life skills mentoring for youth who had experienced different types of trauma. This led us both to want to help others in a different environment, where individuals can be empowered to take responsibility over their own healing. To us, massage is a type of manipulation physical therapy, that encourages healing on many levels.

Advice to any massage client-
The most important thing to 'us', as Licenced providers is to get you on to our table to show you our skills. But a good therapist never forgets that it's not about what we do for you, but what we can facilitate for you. Your health and healing has nothing to do with us. It is yours, not ours. Identify what your goals are with any Therapist, and know what the end looks like. Progress should be tangible, such as range of motion, and decreased pain.

Lina and Paul at Kestrel Way are awesome! I recently had open heart surgery, and Lina worked on me to increase my range of motion while helping with the pinched nerve from my arm being in the same position for so long during my surgery. My wife drives a lot for work, and Paul has helped decrease her neck and lower back pain immensely. They are seriously the best therapists I have ever worked with. I would recommend them to anyone who needs anything from stress relief to a medical massage treatment. They are professional, up beat, easy going, and always on time. And, I love that they meet us where ever we like! We did a staycation recently, where they came to our hotel to give us relaxation massages. Although usually they come to our home, where we focus on pain related issues. We will continue to work with them for a long, long time.

Target Market(s)

Mobile massage therapy clients

Industry/Entity Type

Massage Therapy

Coding

Coded - Design and coding required

Number of Pages Required

1 page

Font styles to use
Serif
Sans Serif

Requirements
Must have
• Please add or remove any information that would help the presentation of our website. Our logo is posted below, please include into the website.
• Please include a contact field that includes, kestrelwaymassage@fernmail.net,
• (206) 555-0148
• We have also included our own stock photos, as well as a photo of Paul and Lina. Please include a cropped photo of both massage therapists.

```html
<!DOCTYPE html>
<html lang="en">
<head>
<meta charset="utf-8">
<title>Kestrel Way – Mobile Massage</title>
<link href="https://fonts.googleapis.com/css2?family=Dancing+Script:wght@700&family=Roboto:wght@400;500;700&family=Open+Sans:wght@400&display=swap" rel="stylesheet">
<style>
:root{
  --teal:#1fc2b8;
  --navy:#1b22b8;
  --black:#000;
  --ink:#222;
  --muted:#555;
  --white:#fff;
  --line:#d8d8d8;
  --bar:#efefef;
}
*{box-sizing:border-box;margin:0;padding:0}
html,body{width:1200px;height:3704px;overflow:hidden}
body{position:relative;background:var(--white);font-family:'Roboto',sans-serif;color:var(--ink)}
.abs{position:absolute}
.script{font-family:'Dancing Script',cursive;font-weight:700}

/* top bar */
.topbar{left:0;top:0;width:1200px;height:52px;background:var(--black);display:flex;justify-content:center;align-items:center;gap:22px}
.topbar span{width:11px;height:11px;border-radius:50%;background:var(--white)}

/* nav */
.nav{left:0;top:52px;width:1200px;height:136px;background:var(--white)}
.nav a{position:absolute;top:60px;font-size:15px;color:var(--ink);text-decoration:none}
.nav a.active{color:var(--teal)}
.nav .active-bar{position:absolute;left:152px;top:0;width:74px;height:5px;background:var(--teal)}
.brand{left:538px;top:4px;width:124px;height:124px;border-radius:50%;background:var(--navy);display:flex;align-items:center;justify-content:center;text-align:center;color:var(--white);font-family:'Roboto',sans-serif;font-weight:700;font-size:21px;line-height:1.1}

/* hero */
.hero{left:0;top:188px;width:1200px;height:469px;background:linear-gradient(135deg,#6b5138 0%,#9a7657 30%,#c6a988 55%,#7c6049 80%,#4a3726 100%)}
.hero .arrow{position:absolute;top:215px}
.hero .pager{position:absolute;left:310px;top:432px;width:580px;height:1px;background:rgba(255,255,255,.6)}
.hero .dots{position:absolute;left:563px;top:427px;display:flex;gap:7px}
.hero .dots i{width:11px;height:11px;border-radius:50%;background:#111;border:2px solid #111}
.hero .dots i.on{background:transparent;border-color:#111}

/* headings */
.heading{left:0;width:1200px;display:flex;justify-content:center;align-items:center;gap:26px;color:var(--teal);font-size:56px}
.heading::before,.heading::after{content:"";width:100px;height:2px;background:var(--teal)}
.heading.light{color:var(--white)}
.heading.light::before,.heading.light::after{background:var(--white)}

/* services */
.service{width:457px;height:192px;border:1px solid var(--teal);background:var(--white);overflow:hidden}
.service .thumb{position:absolute;left:0;top:0;width:260px;height:100%}
.service h3{position:absolute;left:146px;top:36px;font-size:19px;font-weight:400;text-transform:uppercase;color:#111}
.service p{position:absolute;left:146px;top:70px;width:290px;font-size:13.5px;line-height:1.65;color:#333}

/* about */
.about{left:0;top:1264px;width:1200px;height:415px;background:linear-gradient(90deg,#2d1f14 0%,#5b4330 45%,#8a6a4f 75%,#3b2a1d 100%)}
.about .heading{top:78px;width:740px;justify-content:center}
.about .heading::before,.about .heading::after{width:90px}
.about p{position:absolute;left:81px;top:175px;width:650px;font-size:15px;line-height:1.95;color:var(--white)}
.polaroid{background:var(--white);padding:12px 12px 38px;box-shadow:0 6px 14px rgba(0,0,0,.45)}
.polaroid div{width:100%;height:100%}

/* rate */
.rate{width:190px;height:190px}
.rate text{font-family:'Roboto',sans-serif;font-size:22px;fill:#222}

/* education */
.education{left:0;top:2064px;width:1200px;height:417px;background:linear-gradient(120deg,#1c2420 0%,#3a4540 40%,#6d6a60 65%,#26221d 100%)}
.education p{position:absolute;left:140px;top:175px;width:920px;text-align:center;font-size:14px;line-height:1.9;color:var(--white)}
.btn{display:flex;align-items:center;justify-content:center;width:188px;height:62px;font-size:17px;font-weight:500;letter-spacing:.5px;text-transform:uppercase}
.btn.outline-light{border:1px solid var(--white);color:var(--white)}
.btn.outline-dark{border:1px solid #333;color:#222;background:rgba(255,255,255,.35)}

/* testimonial */
.quote{left:0;top:2602px;width:1200px;text-align:center;font-size:58px;font-family:Georgia,serif;color:#111;line-height:1}
.testimonial-text{left:140px;top:2660px;width:920px;text-align:center;font-size:14px;line-height:1.95;color:#222}
.author{left:0;top:2742px;width:1200px;text-align:center;font-size:17px;font-weight:700}
.t-dots{left:540px;top:2802px;display:flex;gap:9px}
.t-dots i{width:11px;height:11px;background:#111;border:2px solid #111}
.t-dots i.on{background:transparent}

/* contact */
.contact{left:0;top:2869px;width:1200px;height:415px;background:linear-gradient(90deg,#cfccc6 0%,#ece9e3 30%,#f7f5f1 60%,#dcd7cf 100%)}
.field{position:absolute;font-size:14px;color:#222;border-bottom:1px solid #444}
.contact-bar{left:0;top:3284px;width:1200px;height:106px;background:var(--bar);font-family:'Open Sans',sans-serif;font-size:21px;color:#222}
.contact-bar .item{position:absolute;top:39px;display:flex;align-items:center;gap:26px}

/* footer */
.footer{left:0;top:3390px;width:1200px;height:314px;background:var(--black)}
.footer .brand{left:550px;top:49px;width:100px;height:100px;font-size:17px;border:3px solid var(--white)}
.footer .social{position:absolute;top:178px;left:466px;display:flex;gap:17px}
.footer .social i{width:55px;height:55px;border-radius:50%;border:2px solid #cfcfcf}
.footer .social i.fill{background:#2d2d2d}
.footer small{position:absolute;left:0;top:250px;width:1200px;text-align:center;font-size:13px;color:var(--teal)}
</style>
</head>
<body>

<div class="abs topbar" aria-label="Social links"><span></span><span></span><span></span><span></span></div>

<nav class="abs nav">
  <div class="active-bar"></div>
  <a class="active" style="left:152px">Home</a>
  <a style="left:268px">About us</a>
  <a style="left:404px">Our Rate</a>
  <div class="abs brand">Kestrel<br>Way</div>
  <a style="left:713px">Education</a>
  <a style="left:856px">Testimonial</a>
  <a style="left:999px">Contact Us</a>
</nav>

<section class="abs hero" role="img" aria-label="Photo of a therapist massaging a client's back">
  <svg class="arrow" style="left:14px" width="50" height="46" viewBox="0 0 50 46" fill="none" stroke="#fff" stroke-width="2.5"><path d="M20 2H48V44H20"/><path d="M36 23H4M14 13L4 23L14 33"/></svg>
  <svg class="arrow" style="right:14px" width="50" height="46" viewBox="0 0 50 46" fill="none" stroke="#fff" stroke-width="2.5"><path d="M30 2H2V44H30"/><path d="M14 23H46M36 13L46 23L36 33"/></svg>
  <div class="pager"></div>
  <div class="dots"><i></i><i class="on"></i><i></i><i></i></div>
</section>

<h2 class="abs heading script" style="top:700px">Services</h2>

<article class="abs service" style="left:136px;top:802px">
  <div class="thumb" role="img" aria-label="Photo of a neuromuscular therapy session" style="background:linear-gradient(90deg,#9fb7ad 0%,#c9d3cd 45%,rgba(255,255,255,0) 100%)"></div>
  <h3>Neuromuscular</h3>
  <p>Lorem ipsum dolor sit amet, consectetur adipiscing elit, sed do eiusmod tempor incididunt ut labore et dolore magna aliqua.</p>
</article>
<article class="abs service" style="left:605px;top:802px">
  <div class="thumb" role="img" aria-label="Photo of a spontaneous muscle release session" style="background:linear-gradient(90deg,#c7a98e 0%,#e0d6cc 45%,rgba(255,255,255,0) 100%)"></div>
  <h3>Spontaneous Muscle Release</h3>
  <p>Lorem ipsum dolor sit amet, consectetur adipiscing elit, sed do eiusmod tempor incididunt ut labore et dolore magna aliqua.</p>
</article>
<article class="abs service" style="left:136px;top:1005px">
  <div class="thumb" role="img" aria-label="Photo of a postural restoration treatment" style="background:linear-gradient(90deg,#6f86a8 0%,#c2c8d2 45%,rgba(255,255,255,0) 100%)"></div>
  <h3>Postural Restoration</h3>
  <p>Lorem ipsum dolor sit amet, consectetur adipiscing elit, sed do eiusmod tempor incididunt ut labore et dolore magna aliqua.</p>
</article>
<article class="abs service" style="left:605px;top:1005px">
  <div class="thumb" role="img" aria-label="Photo of a medical massage treatment" style="background:linear-gradient(90deg,#3f7a66 0%,#b7c9bf 45%,rgba(255,255,255,0) 100%)"></div>
  <h3>Medical Massage</h3>
  <p>Lorem ipsum dolor sit amet, consectetur adipiscing elit, sed do eiusmod tempor incididunt ut labore et dolore magna aliqua.</p>
</article>

<section class="abs about" role="img" aria-label="Background photo of a relaxing massage">
  <h2 class="abs heading light script">Know About Us</h2>
  <p>We are a male and female mobile massage team. Our names are Paul and Lina. Kestrel Way is a Seattle based mobile massage service. Our massage is offered to the community with a goal of facilitating balance within each individual. We specialize in integrated Pain management, and sports/medical massage therapy. Every client's first assessment is attended by our male and female massage therapist team.</p>
  <div class="abs polaroid" style="left:735px;top:30px;width:230px;height:230px;transform:rotate(-7deg)"><div role="img" aria-label="Photo of Paul" style="background:linear-gradient(135deg,#8fa3b6,#5f6f7d)"></div></div>
  <div class="abs polaroid" style="left:870px;top:120px;width:255px;height:250px;transform:rotate(6deg)"><div role="img" aria-label="Photo of Lina" style="background:linear-gradient(135deg,#a3a56a,#6b6541)"></div></div>
</section>

<h2 class="abs heading script" style="top:1722px">Our Rate</h2>
<svg class="abs rate" style="left:293px;top:1831px" viewBox="0 0 190 190" aria-label="75 dollars for 60 minutes"><circle cx="95" cy="95" r="84" fill="none" stroke="#1b22b8" stroke-width="5"/><path d="M18 140A90 90 0 0 1 120 8" fill="none" stroke="#1fc2b8" stroke-width="5"/><text x="95" y="92" text-anchor="middle">$ 75 / 60</text><text x="95" y="120" text-anchor="middle">Minutes</text></svg>
<svg class="abs rate" style="left:505px;top:1831px" viewBox="0 0 190 190" aria-label="95 dollars for 90 minutes"><circle cx="95" cy="95" r="84" fill="none" stroke="#1b22b8" stroke-width="5"/><path d="M18 140A90 90 0 0 1 120 8" fill="none" stroke="#1fc2b8" stroke-width="5"/><text x="95" y="92" text-anchor="middle">$ 95 / 90</text><text x="95" y="120" text-anchor="middle">Minutes</text></svg>
<svg class="abs rate" style="left:717px;top:1831px" viewBox="0 0 190 190" aria-label="120 dollars for 120 minutes"><circle cx="95" cy="95" r="84" fill="none" stroke="#1b22b8" stroke-width="5"/><path d="M18 140A90 90 0 0 1 120 8" fill="none" stroke="#1fc2b8" stroke-width="5"/><text x="95" y="92" text-anchor="middle">$ 120 / 120</text><text x="95" y="120" text-anchor="middle">Minutes</text></svg>

<section class="abs education" role="img" aria-label="Background photo of a wooden sign and greenery">
  <h2 class="abs heading light script" style="top:48px">Our Education</h2>
  <p>We are both Graduates of Venmora, school of massage therapy. We have continuing education in medical massage, myofacial release, trigger point therapy, postural restoration, anatomy, and spontaneous muscle release. Lina is also a Certified Yoga Instructor, which amplifies her experience with flexibility and strength as it pertains to each individual. Paul's passion is Massage, stretching, and strength training to encourage postural restoration and realignment.</p>
  <div class="abs btn outline-light" style="left:506px;top:286px">Read More</div>
</section>

<h2 class="abs heading script" style="top:2510px">Testimonial</h2>
<div class="abs quote">&ldquo;</div>
<p class="abs testimonial-text">Lina and Paul at Kestrel Way are awesome! I recently had open heart surgery, and Lina worked on me to increase my range of motion while helping with the pinched nerve from my arm being in the same position for so long during my surgery. My wife drives a lot for work, and Paul has helped decrease her neck and lower back pain immensely. They are seriously the best therapists I have ever worked with</p>
<div class="abs author">- Darcy T.</div>
<div class="abs t-dots"><i></i><i class="on"></i><i></i><i></i><i></i><i></i></div>

<section class="abs contact" role="img" aria-label="Background photo of a bright massage studio">
  <h2 class="abs heading script" style="top:40px">Keep In Touch</h2>
  <div class="field" style="left:259px;top:150px;width:346px;padding-bottom:6px">Name</div>
  <div class="field" style="left:622px;top:150px;width:360px;padding-bottom:6px">Email Id</div>
  <div class="field" style="left:259px;top:190px;width:723px;height:78px">Message</div>
  <div class="abs btn outline-dark" style="left:506px;top:284px">Submit</div>
</section>

<section class="abs contact-bar">
  <div class="item" style="left:254px">
    <svg width="22" height="22" viewBox="0 0 24 24" fill="#1fc2b8" aria-hidden="true"><path d="M6.6 10.8a15.1 15.1 0 0 0 6.6 6.6l2.2-2.2c.3-.3.7-.4 1-.2 1.1.4 2.3.6 3.6.6.6 0 1 .4 1 1V20c0 .6-.4 1-1 1A17 17 0 0 1 3 4c0-.6.4-1 1-1h3.5c.6 0 1 .4 1 1 0 1.3.2 2.5.6 3.6.1.3 0 .7-.2 1z"/></svg>
    <span>(206) 555-0148</span>
  </div>
  <div class="item" style="left:598px">
    <svg width="22" height="18" viewBox="0 0 24 18" aria-hidden="true"><rect width="24" height="18" rx="2" fill="#1fc2b8"/><path d="M1 2l11 8 11-8" fill="none" stroke="#efefef" stroke-width="2"/></svg>
    <span>kestrelwaymassage@fernmail.net</span>
  </div>
</section>

<footer class="abs footer">
  <div class="abs brand">Kestrel<br>Way</div>
  <div class="social" aria-label="Social links"><i class="fill"></i><i></i><i></i><i></i></div>
  <small>© Kestrel Way mobile massage - 2015. All rights reserved.</small>
</footer>

</body>
</html>
```